Explosive, chemical reaction of creativity!

Web design for a digital marketing company. The unconventional is encouraged!
This is for a cool, young, geographically diverse company (sketchhive... you are all part of our team!!!)... we build websites but our real specialty is "search experience optimization".... creating conversion focused content, SEO (including content), and social media.

Target Market(s)

small to medium size businesses, law firms, medical practices, municipalities

Industry/Entity Type

Marketing

Number of Pages Required

2 page

Requirements
Must have
• WOW
• something different and special... we've been playing with a science theme (www.fernquillmedia.marketing) but we are open to different looks, layouts, etc.
• we nee a homepage design and an interior page design
• content needs to include: Marketing Catalysts (about us), Our Formula (services), Chemical Reactions(Results/Our Clients),
• FREE Online Prism Check
• Let us put together an objective snapshot of your digital presence for you.
Nice to have
• we are open to the use of background video (chemical reaction???)
• we are open to cool and different imagery
Should not have
• template look like most other websites

```html
<!DOCTYPE html>
<html lang="en">
<head>
<meta charset="utf-8">
<title>Fernquill Media Marketing</title>
<link href="https://fonts.googleapis.com/css2?family=Open+Sans:wght@300;400;600;700&display=swap" rel="stylesheet">
<style>
:root{
  --navy:#0e1722;
  --navy-2:#16212e;
  --band:#1b2632;
  --blue:#1f6db3;
  --blue-dark:#18598f;
  --orange:#f08a24;
  --ink:#2a2f36;
  --muted:#6b737c;
  --line:#e3e6ea;
  --white:#ffffff;
}
*{box-sizing:border-box;margin:0;padding:0}
html,body{width:1200px;height:2656px;overflow:hidden}
body{font-family:"Open Sans",Arial,sans-serif;color:var(--ink);background:var(--white);position:relative}
a{color:inherit;text-decoration:none}

/* header */
.site-header{position:absolute;top:0;left:0;width:1200px;height:72px;display:flex;align-items:center;justify-content:space-between;padding:0 40px;z-index:2;background:rgba(10,16,24,.55)}
.brand{display:flex;align-items:center;gap:10px;color:var(--white);font-weight:700;font-size:20px;letter-spacing:.5px}
.brand-mark{width:22px;height:22px;background:var(--blue)}
.main-nav{display:flex;gap:4px}
.main-nav a{font-size:13px;color:var(--white);padding:8px 14px}
.main-nav a.active{background:var(--blue)}

/* hero */
.hero{position:absolute;top:0;left:0;width:1200px;height:600px;background:radial-gradient(circle at 28% 45%,#5a7390 0%,#243447 35%,#0b1119 75%)}
.hero-copy{position:absolute;right:80px;top:220px;width:520px;text-align:right;color:var(--white)}
.hero-copy h1{font-weight:300;font-size:40px;line-height:1.2}
.hero-copy p{font-size:13px;line-height:1.6;margin-top:18px;color:#cdd6e0}
.hero-arrows{position:absolute;right:80px;top:405px;display:flex;gap:14px}

/* cta bars */
.cta-bar{position:absolute;left:0;width:1200px;background:var(--blue);display:flex;align-items:center;justify-content:center;gap:40px;color:var(--white)}
.cta-bar.prism{top:600px;height:88px;font-size:26px;font-weight:300}
.cta-bar.snapshot{top:1540px;height:56px;font-size:18px;font-weight:300}
.btn{display:inline-block;background:var(--orange);color:var(--white);font-size:12px;font-weight:700;text-transform:uppercase;padding:10px 26px}
.btn.small{padding:7px 16px;font-size:11px;background:var(--blue)}

/* welcome */
.welcome{position:absolute;top:688px;left:0;width:1200px;height:652px}
.section-title{text-align:center;font-size:30px;font-weight:400;letter-spacing:.5px;color:var(--ink)}
.welcome .section-title{margin-top:48px}
.section-sub{text-align:center;font-size:15px;color:var(--muted);margin-top:6px}
.phone{position:absolute;left:140px;top:150px;width:220px;height:380px;border-radius:26px;background:linear-gradient(160deg,#2b2f35,#0d0f12)}
.welcome-body{position:absolute;left:430px;top:145px;width:640px}
.welcome-body h3{font-size:15px;font-weight:700;margin-bottom:8px}
.welcome-body p{font-size:12px;line-height:1.7;color:var(--muted)}
.formula{margin-top:18px}
.features{display:flex;gap:30px;margin-top:22px}
.feature{flex:1;display:flex;gap:10px}
.feature-icon{flex:0 0 34px;height:34px;border-radius:50%;background:var(--blue)}
.feature h4{font-size:13px;font-weight:700;margin-bottom:4px}
.feature p{font-size:11px;line-height:1.6}

/* stats */
.stats{position:absolute;top:1340px;left:0;width:1200px;height:200px;background:var(--band);display:flex;justify-content:center;align-items:center;gap:60px;color:var(--white)}
.stat{display:flex;align-items:center;gap:14px;width:230px}
.stat strong{display:block;font-size:44px;font-weight:300;line-height:1}
.stat span{display:block;font-size:10px;color:#9aa5b1;line-height:1.5;margin-top:6px}

/* posts */
.posts{position:absolute;top:1596px;left:0;width:1200px;height:594px}
.posts .section-title{margin-top:56px}
.post-grid{display:flex;justify-content:center;gap:40px;margin-top:40px}
.post{width:300px}
.post-image{height:200px}
.post h3{font-size:17px;font-weight:600;line-height:1.35;margin:16px 0 8px}
.post p{font-size:11px;line-height:1.65;color:var(--muted);margin-bottom:14px}

/* footer */
.site-footer{position:absolute;top:2190px;left:0;width:1200px;height:410px;background:var(--navy);color:#c4ccd5;display:flex;justify-content:center;gap:70px;padding-top:56px}
.footer-col{width:300px}
.footer-col h5{font-size:15px;font-weight:700;color:var(--white);letter-spacing:1px;margin-bottom:18px}
.footer-col p{font-size:11px;line-height:1.7;margin-bottom:12px}
.read-more{font-size:11px;font-weight:700;color:var(--white);display:flex;align-items:center;gap:8px}
.contact-line{display:flex;align-items:flex-start;gap:10px;font-size:12px;line-height:1.5;margin-bottom:12px}
.contact-line svg{flex:0 0 auto;margin-top:2px}
.socials{display:flex;gap:8px;margin:6px 0 18px}
.socials span{width:22px;height:22px;background:var(--navy-2);border:1px solid #34414f}
.field{height:30px;background:var(--white);margin-bottom:10px;font-size:11px;color:#888;padding:8px 10px}
.field.area{height:70px}
.send{background:var(--blue);color:var(--white);font-size:12px;font-weight:700;text-align:center;padding:9px 0}
.copyright{position:absolute;top:2600px;left:0;width:1200px;height:56px;background:#0a1119;color:#7d8792;font-size:11px;display:flex;align-items:center;padding-left:40px}
</style>
</head>
<body>

<section class="hero">
  <div role="img" aria-label="Hand holding a glowing tablet surrounded by floating digital icons" style="position:absolute;inset:0"></div>
  <div class="hero-copy">
    <h1>It's not rocket science,<br>it's Fernquill Media science!</h1>
    <p>Data is the chemical reaction that results from "our formula" which is the<br>right combination of our digital marketing services.</p>
  </div>
  <div class="hero-arrows">
    <svg width="12" height="20" viewBox="0 0 12 20"><path d="M10 2 2 10l8 8" stroke="#fff" stroke-width="2" fill="none"/></svg>
    <svg width="12" height="20" viewBox="0 0 12 20"><path d="M2 2l8 8-8 8" stroke="#fff" stroke-width="2" fill="none"/></svg>
  </div>
</section>

<header class="site-header">
  <a class="brand" href="#"><span class="brand-mark"></span>Fernquill Media Marketing</a>
  <nav class="main-nav">
    <a class="active" href="#">Home</a>
    <a href="#">Marketing Catalysts</a>
    <a href="#">Our Formula</a>
    <a href="#">Chemical Reactions</a>
    <a href="#">Contact Us</a>
  </nav>
</header>

<div class="cta-bar prism">FREE Online Prism Check <a class="btn" href="#">Test Now</a></div>

<section class="welcome">
  <h2 class="section-title">WELCOME TO OUR SITE</h2>
  <p class="section-sub">Using data for success</p>
  <div class="phone" role="img" aria-label="Smartphone showing the agency website"></div>
  <div class="welcome-body">
    <h3>Search Engine Optimization has been replaced with Search Experience Optimization</h3>
    <p>SXO is the next level of everything we do. It is data combined with content, design and strategy. It's not about ranking alone, it's about how people feel when they find you. We blend search data, site structure and useful content so that every visit leads somewhere. Our team builds the experience first, then lets the numbers show us what to improve. That is how small and medium businesses grow with confidence and clarity.</p>
    <h3 class="formula">The Perfect Digital Marketing Formula!</h3>
    <p>Get the right message in front of the right people.</p>
    <div class="features">
      <div class="feature"><span class="feature-icon"></span><div><h4>Website</h4><p>The base of every reaction is a fast, clear site built to convert visitors into leads.</p></div></div>
      <div class="feature"><span class="feature-icon"></span><div><h4>Content</h4><p>Content is the fuel. We write pages and posts that people and search engines value.</p></div></div>
      <div class="feature"><span class="feature-icon"></span><div><h4>Social</h4><p>We spread the word where your audience spends time and keep them talking about you.</p></div></div>
    </div>
  </div>
</section>

<section class="stats">
  <div class="stat"><svg width="40" height="40" viewBox="0 0 40 40"><rect x="4" y="8" width="32" height="22" fill="none" stroke="#fff" stroke-width="2"/><path d="M14 34h12" stroke="#fff" stroke-width="2"/></svg><div><strong>93%</strong><span>Of online experiences begin<br>with a search engine</span></div></div>
  <div class="stat"><svg width="40" height="40" viewBox="0 0 40 40"><path d="M6 30l10-10 6 6 12-14" stroke="#fff" stroke-width="2" fill="none"/></svg><div><strong>70%</strong><span>Of the links search users<br>click on are organic</span></div></div>
  <div class="stat"><svg width="40" height="40" viewBox="0 0 40 40"><circle cx="20" cy="20" r="13" fill="none" stroke="#fff" stroke-width="2"/><path d="M20 12v8h7" stroke="#fff" stroke-width="2" fill="none"/></svg><div><strong>70%</strong><span>Of mobile searches lead to<br>action within one hour</span></div></div>
  <div class="stat"><svg width="40" height="40" viewBox="0 0 40 40"><path d="M8 32V20M16 32V12M24 32V16M32 32V8" stroke="#fff" stroke-width="3"/></svg><div><strong>50%</strong><span>Of consumers are more<br>likely to click a known brand</span></div></div>
</section>

<div class="cta-bar snapshot">Let us put together an objective snapshot of your digital presence for you. <a class="btn" href="#">More</a></div>

<section class="posts">
  <h2 class="section-title">MORE FROM US</h2>
  <div class="post-grid">
    <article class="post">
      <div class="post-image" role="img" aria-label="Keyboard with a social network key" style="background:linear-gradient(135deg,#3a8fd0,#1c3d5e)"></div>
      <h3>A Little Bird Told Me – 5 Reasons for Tweeting</h3>
      <p>There's a lot that short posts can do for your business. Sometimes the few words you share bring more attention than a long page ever could.</p>
      <a class="btn small" href="#">Read More</a>
    </article>
    <article class="post">
      <div class="post-image" role="img" aria-label="Dark laptop keyboard with a glowing key" style="background:linear-gradient(135deg,#2a2e33,#0b0d10)"></div>
      <h3>The Revolution Will Not Be Televised</h3>
      <p>With the advancement of technology, the internet and search engines, consumers have sought out new ways to find the services they need.</p>
      <a class="btn small" href="#">Read More</a>
    </article>
    <article class="post">
      <div class="post-image" role="img" aria-label="Smartphone resting on a desk" style="background:linear-gradient(135deg,#c9ced4,#7f8790)"></div>
      <h3>Searchly's Fast-Loading Tech Encourages New Standard for Mobile Platforms</h3>
      <p>Do you ever feel frustrated waiting for pages to load on your phone? You are not the only one, and search engines have noticed.</p>
      <a class="btn small" href="#">Read More</a>
    </article>
  </div>
</section>

<footer class="site-footer">
  <div class="footer-col">
    <h5>WHO WE ARE</h5>
    <p>Fernquill Media is a young, geographically diverse digital marketing team building websites and search experiences.</p>
    <p>We create conversion focused content, search optimization and social media for small businesses, law firms, medical practices and municipalities.</p>
    <a class="read-more" href="#"><svg width="10" height="10" viewBox="0 0 10 10"><path d="M2 1l5 4-5 4" stroke="#fff" stroke-width="2" fill="none"/></svg>READ MORE</a>
  </div>
  <div class="footer-col">
    <h5>CONTACT</h5>
    <div class="contact-line"><svg width="14" height="14" viewBox="0 0 14 14"><rect x="1" y="3" width="12" height="8" fill="none" stroke="#c4ccd5"/><path d="M1 3l6 5 6-5" stroke="#c4ccd5" fill="none"/></svg><span>info@fernquillmedia.marketing</span></div>
    <div class="contact-line"><svg width="14" height="14" viewBox="0 0 14 14"><path d="M3 1h3l1 3-2 1a7 7 0 0 0 4 4l1-2 3 1v3a2 2 0 0 1-2 2A11 11 0 0 1 1 3a2 2 0 0 1 2-2z" fill="#c4ccd5"/></svg><span>800-555-0148</span></div>
    <div class="socials"><span></span><span></span><span></span><span></span><span></span><span></span></div>
    <div class="contact-line"><svg width="14" height="16" viewBox="0 0 14 16"><path d="M7 15s5-5 5-9A5 5 0 0 0 2 6c0 4 5 9 5 9z" fill="#c4ccd5"/><circle cx="7" cy="6" r="2" fill="#0e1722"/></svg><span>88 Larkspur Avenue, Suite 5<br>Millbrook, OR 97000</span></div>
  </div>
  <div class="footer-col">
    <h5>QUICK CONTACT US</h5>
    <div class="field">Name</div>
    <div class="field">Email Address</div>
    <div class="field area">Message</div>
    <div class="send">SEND IT NOW</div>
  </div>
</footer>

<div class="copyright">Copyright 2016 Fernquill Media. All Rights Reserved.</div>

</body>
</html>
```